The Harbourlight Dental centre, the Zorvik of dentistry

New concept of running a dental practice by having a walk in practice
WE ARE A HUSBAND AND WIFE TEAM

Really modern and sophisticated, we want it to feel different from the traditional dental practice.
we want it split into different pages:CONTACT US
LOCATION: Information about our location since patients often confuse us with the practice across the road
ABOUT US:
Opening hours - & 7 Days, We offer a weekend service
WALK IN: We offer a walk in service for dental treatments
TREATMENTS we offer

DENTAL ADVICE: Free dentist advise call back- So a dentist will call you back for free to discuss

Target Market(s)

Everyone

Industry/Entity Type

Dental

Coding

Coded - Design and coding required

Number of Pages Required

5+ page

Requirements
Must have
• First page
• * changing pictures
• *opening times
• * our walk in concept I.e. no appointment needed
• *logo
• * links in to clinic tidal (online booking system in Australia)
• * address /phone number/email
• * possible videos
• Second page
• meet the team
• third page
• dental treatments/walk in treatments
• fourth page
• dental advice with vid larko videos
• Fifth page
• contact us/maps/ we get confused with the dental practice across the road
• We would also like a giving back page. In this please include the photo's below of our dental mission in Guatemala, where by we did treatment for patients as part of a charity.
Nice to have
• Changing pictures on the home screen
• videos linked to home page

```html
<!DOCTYPE html>
<html lang="en">
<head>
<meta charset="utf-8">
<title>The Harbourlight Dental Centre</title>
<link rel="stylesheet" href="https://fonts.googleapis.com/css2?family=Raleway:wght@400;500;600&family=Open+Sans:wght@400;600&display=swap">
<style>
:root{
  --blue:#1aa3e8;
  --blue-dark:#0a88d0;
  --green:#6cc332;
  --green-dark:#52a822;
  --ink:#333;
  --muted:#8a8a8a;
  --light:#f1f1f1;
  --rule:#dcdcdc;
}
*{box-sizing:border-box;margin:0;padding:0}
html,body{width:683px;height:1200px;overflow:hidden;background:#fff}
body{position:relative;font-family:"Open Sans",Arial,sans-serif;color:var(--ink)}
.abs{position:absolute}
.brand{display:flex;align-items:center;gap:7px;font-family:"Raleway",sans-serif;font-weight:600;color:var(--green);line-height:1.1}
.brand .dot{width:16px;height:16px;border-radius:50%;background:var(--blue);flex:none}
.header-brand{left:66px;top:18px;font-size:14px;width:150px}
.footer-brand{left:63px;top:1072px;font-size:15px;width:160px}
.hours{left:370px;top:27px;font-size:8px;color:#444}
.hours span{display:flex;align-items:center;gap:3px;color:var(--blue);font-size:7px;margin-top:2px}
.call{right:65px;top:21px;text-align:right;font-size:8px;color:var(--green)}
.call b{display:flex;align-items:center;gap:3px;font-weight:400;font-size:12px;color:#444;margin-top:1px}
.nav{left:66px;top:61px;right:0;height:29px;background:linear-gradient(#2ab4f0,var(--blue));display:flex;font-family:"Raleway",sans-serif;font-size:9.5px;color:#fff}
.nav a{padding:0 14px;line-height:29px;border-right:1px solid rgba(255,255,255,.35);text-decoration:none;color:#fff}
.nav a.active{background:var(--blue-dark);width:72px;text-align:center}
.hero{left:0;top:90px;width:683px;height:272px;background:linear-gradient(90deg,#b9c1c1,#8a9b9a 40%,#5b7a9a 60%,#c7cfd1)}
.hero-text{left:69px;top:190px;color:#fff;font-family:"Raleway",sans-serif;text-shadow:0 1px 3px rgba(0,0,0,.3)}
.hero-text p{font-size:15px}
.hero-text h1{font-size:20px;font-weight:500;margin-top:4px}
.dots{left:322px;top:344px;display:flex;gap:3px}
.dots i{width:9px;height:9px;border-radius:50%;background:#fff}
.dots i:first-child{background:var(--green);border:1px solid #fff}
.welcome h2{left:67px;top:395px;font-family:"Raleway",sans-serif;font-weight:400;font-size:15px;color:#333}
.intro{left:69px;top:422px;width:295px;font-size:7px;line-height:16.5px;color:#666}
.intro2{left:69px;top:475px;width:290px;font-size:7px;line-height:10.5px;color:var(--muted)}
.btn-green{left:70px;top:508px;width:71px;height:21px;background:linear-gradient(var(--green),var(--green-dark));color:#fff;font-size:6.5px;font-weight:600;display:flex;align-items:center;justify-content:center;border-radius:2px}
.partner{left:158px;top:512px;font-family:"Raleway",sans-serif;font-size:14px;font-weight:500;color:#333;display:flex;align-items:center;gap:6px}
.partner .dot{width:13px;height:13px;border-radius:50%;background:var(--blue)}
.video{left:384px;top:388px;width:235px;height:150px;background:#1f1f1f}
.video .shot{position:absolute;left:1px;top:1px;right:1px;height:131px;background:linear-gradient(120deg,#e9ecec,#c9d2d2 45%,#8fc46a 60%,#dfe3e3)}
.features{left:0;top:574px;width:683px;height:207px;background:#f0f0f0;border-top:1px solid #e2e2e2;border-bottom:1px solid #e2e2e2}
.feature{top:600px;width:190px;text-align:center}
.feature .ring{width:74px;height:74px;border-radius:50%;margin:0 auto;border:3px solid #fff;box-shadow:0 0 0 2px currentColor;display:flex;align-items:center;justify-content:center}
.feature h3{font-family:"Raleway",sans-serif;font-weight:400;font-size:11.5px;margin-top:10px;color:#333}
.feature p{font-size:7px;line-height:11.5px;color:#999;margin-top:4px}
.btn-outline{display:inline-block;margin-top:9px;width:65px;height:17px;border:1px solid #555;font-size:5.5px;line-height:15px;color:#333}
.card{top:806px;width:175px;height:185px;border:1px solid var(--rule);background:#fff;text-align:center;box-shadow:0 0 2px rgba(0,0,0,.06)}
.card .photo{margin:5px 5px 0;height:90px}
.card h4{font-family:"Raleway",sans-serif;font-weight:400;font-size:11.5px;margin-top:10px;color:#333}
.card p{font-size:6.5px;line-height:11.5px;color:#999;margin:5px 8px 0;height:23px;overflow:hidden}
.btn-blue{display:inline-block;margin-top:10px;width:61px;height:17px;background:var(--blue);color:#fff;font-size:5.5px;font-weight:600;line-height:17px}
.footer{left:0;top:1022px;width:683px;height:144px;background:linear-gradient(#fff,#f3f3f3)}
.col{top:1052px;font-size:6.5px;color:#666;line-height:16px}
.col h5{font-family:"Raleway",sans-serif;font-weight:500;font-size:9.5px;color:var(--blue);line-height:12px;margin-bottom:4px}
.socials{left:352px;top:1121px;display:flex;gap:4px}
.socials i{width:19px;height:19px;border-radius:50%}
.copy{left:0;top:1166px;width:683px;height:34px;background:#ebebeb;font-size:6.5px;color:#666;padding:13px 0 0 93px}
</style>
</head>
<body>
<header class="header">
  <div class="abs brand header-brand"><span class="dot"></span><span>The Harbourlight<br>Dental Centre</span></div>
  <div class="abs hours">Opening times
    <span><svg width="7" height="7" viewBox="0 0 10 10"><circle cx="5" cy="5" r="4" fill="none" stroke="#1aa3e8" stroke-width="1.3"/><path d="M5 2.5V5h2" fill="none" stroke="#1aa3e8" stroke-width="1.2"/></svg>OPEN 8 AM TO 8PM 7 DAYS A WEEK</span>
  </div>
  <div class="abs call">Call Us Now
    <b><svg width="10" height="10" viewBox="0 0 24 24"><path fill="#6cc332" d="M6.6 10.8a15 15 0 006.6 6.6l2.2-2.2c.3-.3.7-.4 1-.2 1.1.4 2.3.6 3.6.6.6 0 1 .4 1 1V20c0 .6-.4 1-1 1A17 17 0 013 4c0-.6.4-1 1-1h3.5c.6 0 1 .4 1 1 0 1.3.2 2.5.6 3.6.1.3 0 .7-.2 1z"/></svg>08 7240 3918</b>
  </div>
  <nav class="abs nav">
    <a class="active">HOME</a><a>MEET THE TEAM</a><a>DENTAL TREATMENT</a><a>DENTAL ADVICE</a><a style="border:0">CONTACT US</a>
  </nav>
</header>

<section class="abs hero" role="img" aria-label="Photo of the two dentists standing together in scrubs at their dental mission"></section>
<div class="abs hero-text"><p>WE OFFER A WALK IN SERVICE</p><h1>FOR DENTAL TREATMENTS</h1></div>
<div class="abs dots"><i></i><i></i><i></i><i></i></div>

<section class="welcome">
  <h2 class="abs">Welcome to The Harbourlight Dental Centre</h2>
  <p class="abs intro">Your general and cosmetic dentist in the heart of vibrant Wendale. Whether it's cosmetic hygiene treatment, tooth whitening, or botox facial rejuvenation. Located within the busy medical centre with free parking all around.</p>
  <p class="abs intro2">Please call or pop in and one of our helpful team will be only too happy to help for all your dental needs.</p>
  <div class="abs btn-green">VIEW VIDEOS</div>
  <div class="abs partner"><span class="dot"></span>clinic tidal</div>
  <div class="abs video">
    <div class="shot" role="img" aria-label="Video still of the treatment room with a green dental chair"></div>
    <svg class="abs" style="left:95px;top:44px" width="46" height="46" viewBox="0 0 46 46"><circle cx="23" cy="23" r="21" fill="none" stroke="#fff" stroke-width="2.5"/><path d="M18 13l13 10-13 10z" fill="none" stroke="#fff" stroke-width="2.5"/></svg>
    <svg class="abs" style="left:0;top:132px" width="235" height="18" viewBox="0 0 235 18"><path d="M6 5l7 4-7 4z" fill="#fff"/><rect x="18" y="7" width="160" height="4" rx="2" fill="#ddd"/><rect x="18" y="7" width="63" height="4" rx="2" fill="#1a6fd0"/><path d="M218 7h2l3-3v10l-3-3h-2z" fill="#fff"/><path d="M225 6q2 3 0 6" stroke="#fff" fill="none"/></svg>
  </div>
</section>

<section class="abs features" role="img" aria-label="Faded background photo of dental treatment"></section>
<div class="abs feature" style="left:54px">
  <div class="ring" style="background:var(--green);color:var(--green)"><svg width="40" height="40" viewBox="0 0 40 40" fill="none" stroke="#fff" stroke-width="2"><circle cx="29" cy="10" r="4"/><path d="M26 13L8 33M30 16L14 34M12 28l3 3"/></svg></div>
  <h3>Dental Treatment</h3>
  <p>We provide all your general dentistry needs.<br>We also offer an emergency service</p>
  <span class="btn-outline">LEARN MORE</span>
</div>
<div class="abs feature" style="left:244px">
  <div class="ring" style="background:var(--blue);color:var(--blue)"><svg width="46" height="20" viewBox="0 0 46 20" fill="none" stroke="#fff" stroke-width="2"><path d="M3 6q20 -4 40 0v6q-20 6-40 0z"/><path d="M12 5v10M23 4v12M34 5v10"/></svg></div>
  <h3>Dental Advice</h3>
  <p>Free dentist advise call back- So a dentist will<br>call you back for free to discuss</p>
  <span class="btn-outline">LEARN MORE</span>
</div>
<div class="abs feature" style="left:433px">
  <div class="ring" style="background:var(--green);color:var(--green)"><svg width="36" height="30" viewBox="0 0 36 30" fill="#fff"><circle cx="18" cy="8" r="5"/><circle cx="8" cy="10" r="4"/><circle cx="28" cy="10" r="4"/><path d="M9 26q0-11 9-11t9 11z"/><path d="M1 24q0-8 7-8 3 0 4 1-4 3-4 7zM35 24q0-8-7-8-3 0-4 1 4 3 4 7z"/></svg></div>
  <h3>Meet the Team</h3>
  <p>We want our patients to feel safe, happy and<br>have dental treatment which is accessible</p>
  <span class="btn-outline">LEARN MORE</span>
</div>

<article class="abs card" style="left:74px">
  <div class="photo" role="img" aria-label="Photo of patients being treated at the charity dental mission" style="background:linear-gradient(#6d7f93,#b8b3ac)"></div>
  <h4>Facial Aesthetics</h4>
  <p>Botox Wrinkle reduction and Derma Fillers at The Harbourlight Dental Centre.</p>
  <span class="btn-blue">READ MORE</span>
</article>
<article class="abs card" style="left:255px">
  <div class="photo" role="img" aria-label="Close-up photo of a smile before and after whitening" style="background:linear-gradient(90deg,#c8554f,#e8ded4 50%,#c8554f)"></div>
  <h4>Teeth Whitening</h4>
  <p>Now you can whiten your smile with our custom fitted whitening trays in the comfort</p>
  <span class="btn-blue">READ MORE</span>
</article>
<article class="abs card" style="left:437px">
  <div class="photo" role="img" aria-label="Group photo of the doctors and volunteer team" style="background:linear-gradient(#e3e0dc,#3e6f9a)"></div>
  <h4>Our Doctors &amp; Team</h4>
  <p>Dr Ashby was the owner of a highly successful Private practice in London. He has extensive</p>
  <span class="btn-blue">READ MORE</span>
</article>

<footer>
  <div class="abs footer"></div>
  <div class="abs brand footer-brand"><span class="dot"></span><span>The Harbourlight<br>Dental Centre</span></div>
  <div class="abs col" style="left:246px"><h5>QUICK LINKS</h5>Home<br>Who we are<br>What we do<br>Client Experiences</div>
  <div class="abs col" style="left:354px"><h5>RESOURCES</h5>Promotions<br>Career Opportunities<br>Contact us</div>
  <div class="abs col" style="left:465px"><h5>CONTACT US</h5>Unit 7, 18 Ferncliff Parade,<br>Wendale, WA 6071,<br>Phone: 08 7240 3918<br>OPEN 8 AM TO 8PM 7 DAYS A WEEK</div>
  <div class="abs socials"><i style="background:#4fb3e8"></i><i style="background:#2d5a9e"></i><i style="background:#1f79a8"></i><i style="background:#d64a3a"></i></div>
  <div class="abs copy">© 2016 Company Name &nbsp;All right reserved</div>
</footer>
</body>
</html>
```